Maple Grove Schools | brand new stationery!

We need stationery design with our new logo! Our company updated it's name and image and we like to incorporate the new one on our stationery, business cards and email signature. We are looking for fresh, new ideas!
Industry: Childcare, Elementary and Middle School
Company Name: Maple Grove Schools
Tagline: Bright Futures Start Here
Main colors: Blue, white and a little yellow
Star shape is something new for us! Do you see a way to incorporate it as a design element?

```html
<!DOCTYPE html>
<html lang="en">
<head>
<meta charset="utf-8">
<title>Maple Grove Schools – Business Card</title>
<link href="https://fonts.googleapis.com/css2?family=Outfit:wght@400;500;600&family=Rubik:wght@300;400&display=swap" rel="stylesheet">
<style>
  :root {
    --backdrop: #a9a9a9;
    --card-white: #ffffff;
    --card-dark: #221f20;
    --ink: #1f1c1d;
    --navy: #031b70;
    --yellow: #fbc02d;
    --body-text: #3b3b3b;
    --silver: #d6d6d6;
  }
  * { box-sizing: border-box; margin: 0; padding: 0; }
  html, body {
    width: 1200px; height: 1200px; overflow: hidden;
    background: var(--backdrop);
  }
  .card {
    position: absolute; left: 257px; width: 686px; height: 392px;
    border-radius: 24px; overflow: hidden;
    box-shadow: 0 16px 30px rgba(0,0,0,0.25);
  }
  .card-front { top: 165px; background: var(--card-white); }
  .card-back { top: 653px; background: var(--card-dark); }

  .wordmark {
    position: absolute; left: 44px; top: 36px;
    font-family: "Outfit", sans-serif; font-weight: 600; color: var(--ink);
    line-height: 1;
  }
  .wordmark .line-one { display: block; font-size: 50px; letter-spacing: -0.5px; }
  .wordmark .line-two { display: block; font-size: 44px; margin: 4px 0 0 56px; }

  .person {
    position: absolute; left: 43px; top: 156px;
    font-family: "Outfit", sans-serif;
  }
  .person-name { font-size: 23px; font-weight: 500; color: var(--navy); letter-spacing: 0.8px; line-height: 1.1; }
  .person-role { font-family: "Rubik", sans-serif; font-size: 15px; color: var(--yellow); line-height: 1.2; }

  .contact-list {
    position: absolute; left: 44px; top: 215px; list-style: none;
    font-family: "Rubik", sans-serif; font-weight: 300; font-size: 15.5px;
    color: var(--body-text); line-height: 19px;
  }
  .contact-list li { display: flex; align-items: flex-start; gap: 9px; }
  .contact-list li.address { margin-bottom: 8px; }
  .contact-list svg { width: 14px; height: 14px; flex: none; margin-top: 3px; fill: var(--navy); }

  .children-art {
    position: absolute; right: 0; top: 20px; width: 355px; bottom: 0;
    background: linear-gradient(160deg, #ffffff 0%, #ffffff 22%, #0b2382 48%, var(--navy) 100%);
  }

  .back-badge {
    position: absolute; left: 50%; top: 86px; width: 104px; height: 104px;
    margin-left: -52px; border-radius: 50%; background: var(--navy);
  }
  .back-name {
    position: absolute; left: 0; right: 0; top: 208px; text-align: center;
    font-family: "Outfit", sans-serif; font-weight: 500; color: var(--silver); line-height: 1;
  }
  .back-name .line-one { display: block; font-size: 56px; }
  .back-name .line-two { display: block; font-size: 50px; margin-top: 8px; }
</style>
</head>
<body>
  <section class="card card-front">
    <h1 class="wordmark"><span class="line-one">Maple Grove</span><span class="line-two">Schools</span></h1>
    <div class="person">
      <p class="person-name">DANIEL BROOKS</p>
      <p class="person-role">President</p>
    </div>
    <ul class="contact-list">
      <li class="address">
        <svg viewBox="0 0 14 14"><path d="M7 0a5 5 0 0 0-5 5c0 3.6 5 9 5 9s5-5.4 5-9a5 5 0 0 0-5-5zm0 7a2 2 0 1 1 0-4 2 2 0 0 1 0 4z"/></svg>
        <span>1420 Birchwood Drive<br>Fairview, Oregon 97024</span>
      </li>
      <li>
        <svg viewBox="0 0 14 14"><path d="M3 1l2.5 0 1 3-1.6 1.2a8 8 0 0 0 3.9 3.9L10 7.5l3 1V11c0 1-1 2-2 2A10 10 0 0 1 1 3c0-1 1-2 2-2z"/></svg>
        <span>555-214-7731</span>
      </li>
      <li>
        <svg viewBox="0 0 14 14"><path d="M3.5 0h7a1 1 0 0 1 1 1v12a1 1 0 0 1-1 1h-7a1 1 0 0 1-1-1V1a1 1 0 0 1 1-1zm.8 1.8v9h5.4v-9z"/></svg>
        <span>555-608-3192</span>
      </li>
      <li>
        <svg viewBox="0 0 14 14"><path d="M3 0h8v4H3zM1 5h12v6h-2v3H3v-3H1zm3 4v3h6V9z"/></svg>
        <span>555-347-9026</span>
      </li>
      <li>
        <svg viewBox="0 0 14 14"><path d="M1 3h12v8H1zm1.2 1.3v.4L7 8l4.8-3.3v-.4z"/></svg>
        <span>hello@maplegroveschools.com</span>
      </li>
      <li>
        <svg viewBox="0 0 14 14"><circle cx="7" cy="7" r="6.5"/><path d="M4 3.5c1.5 0 2 1 1.5 2S3 6 3.5 8s2 1 2 3M9 2.5c-.5 1.5.5 2 1.5 2.5M8 8c1 0 2 .5 1.5 2.5" stroke="#fff" stroke-width="1.1" fill="none"/></svg>
        <span>maplegroveschools.com</span>
      </li>
    </ul>
    <div class="children-art" role="img" aria-label="Large navy silhouette illustration of two children holding hands, with a yellow star above"></div>
  </section>

  <section class="card card-back">
    <div class="back-badge"></div>
    <p class="back-name"><span class="line-one">Maple Grove</span><span class="line-two">Schools</span></p>
  </section>
</body>
</html>
```